Business Card for Professional Photographer

I'm looking for an eye catching modern clean design that compliments my logo/ website fonts & colours.
I specialise in architecture, corporate & commercial photography so I'm marketing to professional clients rather than portrait / wedding clients.

I would prefer to not have a solid black design.

My logo brand guide is as follows :

Main front font. : Reislust
Main font colour : #fff
Slogan front font : Ubuntu Bold
Monogram front font : Venti Medium
Container colour : #fff

I need print ready files in pdf .png & .eps formats.

Included in the files below are some screen grabs as reference to font & colours etc.

```html
<!DOCTYPE html>
<html lang="en">
<head>
<meta charset="utf-8">
<title>Lens &amp; Line – Business Card</title>
<link href="https://fonts.googleapis.com/css2?family=Montserrat:wght@300;400;500;600&display=swap" rel="stylesheet">
<style>
  :root {
    --stage: #e6e6e8;
    --card: #ffffff;
    --ink: #4a4a4c;
    --ink-soft: #6b6b6e;
    --gold: #c9962e;
    --gold-light: #f6e39f;
    --gold-deep: #c8a347;
    --band-dark: #4b4b4d;
    --sky: #b9cde6;
    --haze: #d9dde2;
    --ground: #9a9ca0;
  }
  html, body {
    margin: 0; padding: 0;
    width: 1200px; height: 960px;
    overflow: hidden;
    background: var(--stage);
    font-family: "Montserrat", sans-serif;
  }
  .stage {
    position: relative;
    width: 1200px; height: 960px;
  }
  .card {
    position: absolute;
    left: 250px;
    width: 700px; height: 400px;
    border-radius: 22px;
    overflow: hidden;
    background: var(--card);
    box-shadow: 0 10px 30px rgba(0,0,0,.14);
  }
  .card--front { top: 60px; }
  .card--back { top: 500px; }

  /* front */
  .front-photo {
    position: absolute; inset: 0;
    background: linear-gradient(180deg, var(--sky) 0%, var(--haze) 55%, var(--ground) 100%);
  }
  .front-veil {
    position: absolute; inset: 0;
    background: rgba(255,255,255,.45);
  }
  .brand {
    position: absolute;
    display: flex; align-items: center; gap: 18px;
  }
  .card--front .brand { left: 170px; top: 170px; }
  .brand-square {
    width: 54px; height: 54px;
    border: 3px solid var(--gold);
    border-radius: 6px;
    box-sizing: border-box;
  }
  .brand-name {
    font-weight: 300;
    font-size: 38px;
    letter-spacing: 6px;
    color: var(--ink);
    text-transform: uppercase;
    line-height: 1;
  }
  .brand-tag {
    font-weight: 600;
    font-size: 11px;
    letter-spacing: 2.5px;
    color: var(--ink-soft);
    margin-top: 8px;
  }

  /* back */
  .band {
    position: absolute;
    left: 90px; width: 130px;
  }
  .band--dark { top: 0; height: 200px; background: var(--band-dark); }
  .band--gold {
    top: 285px; bottom: 0;
    background: linear-gradient(90deg, var(--gold-deep) 0%, var(--gold-light) 50%, var(--gold-deep) 100%);
  }
  .band-mark {
    position: absolute;
    left: 115px; top: 212px;
    width: 80px; height: 62px;
    border: 4px solid var(--gold);
    border-radius: 8px;
    box-sizing: border-box;
  }
  .card--back .brand { left: 300px; top: 50px; }
  .card--back .brand-name { font-size: 28px; letter-spacing: 5px; }
  .card--back .brand-tag { font-size: 9px; letter-spacing: 2px; margin-top: 6px; }

  .person { position: absolute; left: 330px; top: 140px; }
  .person-name {
    font-weight: 500; font-size: 20px; letter-spacing: 1px;
    color: var(--gold); text-transform: uppercase; margin: 0;
  }
  .person-role { font-size: 17px; color: var(--ink); margin: 2px 0 0; }
  .address { margin: 22px 0 16px; font-size: 16px; line-height: 1.3; color: var(--ink); font-style: normal; }
  .contacts { list-style: none; margin: 0; padding: 0; }
  .contacts li {
    display: flex; align-items: center; gap: 12px;
    font-size: 16px; line-height: 26px; color: var(--ink);
  }
  .contacts svg { width: 14px; height: 14px; fill: var(--gold); flex: none; }
</style>
</head>
<body>
<main class="stage">

  <section class="card card--front" aria-label="Card front">
    <div class="front-photo" role="img" aria-label="Photograph of a modern white and orange architectural building under a blue sky with a car park in front"></div>
    <div class="front-veil"></div>
    <div class="brand">
      <span class="brand-square"></span>
      <div>
        <div class="brand-name">Lens &amp; Line</div>
        <div class="brand-tag">Architecture Corporate Commercial</div>
      </div>
    </div>
  </section>

  <section class="card card--back" aria-label="Card back">
    <div class="band band--dark"></div>
    <div class="band-mark"></div>
    <div class="band band--gold"></div>

    <div class="brand">
      <div>
        <div class="brand-name">Lens &amp; Line</div>
        <div class="brand-tag">Architecture Corporate Commercial</div>
      </div>
    </div>

    <div class="person">
      <p class="person-name">Daniel Reyes</p>
      <p class="person-role">President</p>
      <address class="address">2140 Cedar Hollow Road<br>Juneau, Alaska 34810</address>
      <ul class="contacts">
        <li><svg viewBox="0 0 24 24"><path d="M6.6 10.8a15.2 15.2 0 0 0 6.6 6.6l2.2-2.2a1 1 0 0 1 1-.25 11.4 11.4 0 0 0 3.6.57 1 1 0 0 1 1 1V20a1 1 0 0 1-1 1A17 17 0 0 1 3 4a1 1 0 0 1 1-1h3.5a1 1 0 0 1 1 1c0 1.25.2 2.45.57 3.6a1 1 0 0 1-.25 1z"/></svg>555-214-7730</li>
        <li><svg viewBox="0 0 24 24"><path d="M7 1h10a2 2 0 0 1 2 2v18a2 2 0 0 1-2 2H7a2 2 0 0 1-2-2V3a2 2 0 0 1 2-2zm0 3v14h10V4zm5 15.5a1 1 0 1 0 0 2 1 1 0 0 0 0-2z"/></svg>555-603-1942</li>
        <li><svg viewBox="0 0 24 24"><path d="M6 2h9l3 3v5H6zM3 11h18v9H3zm3 3v2h4v-2z"/></svg>555-388-2056</li>
        <li><svg viewBox="0 0 24 24"><path d="M2 5h20v14H2zm2 2v.5l8 5 8-5V7z"/></svg>info@lensandline.com</li>
        <li><svg viewBox="0 0 24 24"><circle cx="12" cy="12" r="10"/></svg>www.lensandline.com</li>
      </ul>
    </div>
  </section>

</main>
</body>
</html>
```